Label and packaging - Lune de Sable

We are after label and pack design for a product called Lune de Sable. This product is a blend of Pinot Gris and Apple Cider.

Lune de Sable:

The packaging needs to accomplish the following: quickly explain what the product is, establish as a premium price product and grab the eye. The package should also reflect the product innovation.

Quickly Explain What the Product Is:

Lune de Sable is a nice name that could lift the image – but no one will have any idea what the product is by the name. Consider that a consumer will be staring at a shelf, then the bottle for maybe two to three seconds before moving on to another bottle. In those three seconds we need to make certain that they understand that the product is a blend of wine and cider. Lune de Sable will not support this on its own.

Suggestion is to use words like Wine, Cider, Orchard, Vine, Apple, Heirloom, Exotic and make it simple. Perhaps a sticker that says “50% Wine/50% Apple Cider” that sits on the neck of every bottle. They need to quickly ‘get it”. Imagery will assist as well. Consider a hybrid 50/50 image of wine grapes and apples to tell the story.

Establish a Premium Price Point:

The label needs to say high quality in the package and the font. Have fun with the shipper – this is where you can have a field day with imagery and fun buzz words – we love the idea of a busy shipper that tells the story with a clean and smart looking bottle.

Target Market(s)

This is a premium product targeted at females of age 25-45.

Industry/Entity Type

Consumer

Colors
ec1f27
9bcb3c

Requirements
Must have
• Label design on a burgundy bottle with a screw cap, see here for bottle shape: http://www.vk-flaskrange.co.nz/wine/#/?view=thumbs&segments=41&colors=&capacityMin=187&capacityMax=750&heightMin=171&heightMax=334&labelMin=44&labelMax=168&neckMin=0&neckMax=1000

Packaging design on a 12 x 750ml carton. This sort of thing: https://www.barrelnook.com.au/images/photo06.jpg

Nice to have
• We have attached some examples of a concept we quite like but it's not bright enough.

```html
<!DOCTYPE html>
<html lang="en">
<head>
<meta charset="utf-8">
<title>Lune de Sable – Label</title>
<link href="https://fonts.googleapis.com/css2?family=Marcellus+SC&family=Arimo:wght@400&display=swap" rel="stylesheet">
<style>
  :root {
    --glass-centre: #efedcf;
    --glass-mid: #e6e4bf;
    --glass-edge: #d3d19f;
    --plate-gold: #d8c99a;
    --plate-gold-light: #efe4bd;
    --ink: #1c1a17;
    --grape: #8a78c4;
    --grape-deep: #5f4f9c;
    --apple: #f2913a;
    --apple-red: #e4512c;
  }
  * { margin: 0; padding: 0; box-sizing: border-box; }
  html, body {
    width: 1011px;
    height: 1200px;
    overflow: hidden;
    background: var(--glass-mid);
  }
  .label {
    position: relative;
    width: 1011px;
    height: 1200px;
    overflow: hidden;
    background: linear-gradient(90deg, var(--glass-edge) 0%, var(--glass-mid) 12%, var(--glass-centre) 40%, var(--glass-centre) 60%, var(--glass-mid) 88%, var(--glass-edge) 100%);
  }
  .name-plate {
    position: absolute;
    left: 196px;
    top: 156px;
    width: 552px;
    height: 124px;
    background: linear-gradient(180deg, var(--plate-gold-light), var(--plate-gold));
    border: 4px solid var(--ink);
    display: flex;
    align-items: center;
    justify-content: center;
  }
  .name-plate::before {
    content: "";
    position: absolute;
    inset: 8px;
    border: 2px solid var(--ink);
  }
  .brand-name {
    position: relative;
    font-family: "Marcellus SC", serif;
    font-size: 62px;
    letter-spacing: 2px;
    color: var(--ink);
    font-weight: 400;
    white-space: nowrap;
  }
  .descriptor {
    position: absolute;
    left: 196px;
    width: 552px;
    top: 292px;
    text-align: center;
    font-family: "Arimo", sans-serif;
    font-size: 42px;
    line-height: 54px;
    color: var(--ink);
  }
  .fruit-illustration {
    position: absolute;
    left: 110px;
    top: 420px;
    width: 780px;
    height: 780px;
  }
</style>
</head>
<body>
  <main class="label">
    <div class="name-plate">
      <span class="brand-name">LUNE de SABLE</span>
    </div>
    <p class="descriptor">blend of apple cider<br>&amp; pinot gris</p>
    <svg class="fruit-illustration" viewBox="0 0 780 780" role="img" aria-label="Illustration of a bunch of purple grapes and an orange apple surrounded by bubbles">
      <defs>
        <radialGradient id="grape-tone" cx="0.5" cy="0.5" r="0.5">
          <stop offset="0" stop-color="#8a78c4"/>
          <stop offset="0.6" stop-color="#7c6bbb" stop-opacity="0.75"/>
          <stop offset="1" stop-color="#5f4f9c" stop-opacity="0"/>
        </radialGradient>
        <radialGradient id="apple-tone" cx="0.45" cy="0.45" r="0.55">
          <stop offset="0" stop-color="#f2913a"/>
          <stop offset="0.7" stop-color="#e4512c" stop-opacity="0.8"/>
          <stop offset="1" stop-color="#e4512c" stop-opacity="0"/>
        </radialGradient>
      </defs>
      <ellipse cx="210" cy="230" rx="190" ry="200" fill="url(#grape-tone)"/>
      <ellipse cx="470" cy="500" rx="220" ry="230" fill="url(#apple-tone)"/>
    </svg>
  </main>
</body>
</html>
```